Design website for new email startup

We are starting a company called Pingo.QZ (it will live at http://pingo.qz).

We would like the main landing page for our site designed. We have provided a very simple wireframe to help provide direction for the content it should include, but we do not expect the designers to adhere to it at all - we encourage unique ideas. There is some sample text in the wireframe - this does not have to be used, but may provide ideas.

We provide an easy way for people to manage email for a custom domain name. For example if you own "yourhouseword.example" you can point your DNS records to us and we'll make it easy to have emails addressed to your domain get forwarded to your existing email (gmail, etc). Folks running blogs, and other small sites can quickly setup email addresses for their domains and manage them in one place.

(For technical folks, we have you point your dns mx records to us, hence the name. That way all your email hits us and we can redirect it wherever you want. We make it easy to manage a single domain or a bunch of domains. Many domain registrars offer this service for a fee, and have clumsy management tools. We provide a robust simple toolset for free, as well as premium options).

The goal of the landing page is to get folks into the signup flow. The second priority flow is to have them take a look at the premium plan offerings.

We may offer the winning designer additional work for the remainder of the site design.
Updates

I've changed this project to a committed payment.  It is no longer refundable.  Thank you.

Target Market(s)

Bloggers, podcasters, designers, app developers - people who are a little tech savvy.

Industry/Entity Type

It Company

Font styles to use
Sans Serif

Colors

Designer to choose colors to be used in the design.

Requirements
Must have
• A full fidelity mockup (comp) of the landing page including the source file (psd, ai, etc).

Some sort of logo treatment for the pingo.qz brand

A call to action for signup, such as the suggested 'Get Started Here'
Nice to have
• A hip startup feel

Incorporation of the email theme

Give the impression it is simple, easy and fast

```html
<!DOCTYPE html>
<html lang="en">
<head>
<meta charset="utf-8">
<title>Pingo.QZ — Email for your custom domain</title>
<link rel="stylesheet" href="https://fonts.googleapis.com/css2?family=Oswald:wght@500&family=PT+Sans:wght@400;700&family=Sansita:wght@800&display=swap">
<style>
  :root {
    --header-bg: #f2f0f1;
    --ink: #2e2d27;
    --hero-dark: #8a8a8a;
    --hero-light: #e4e4e4;
    --green: #8cc63f;
    --green-dark: #6aa51e;
    --orange: #f7a95a;
    --orange-deep: #f08a2a;
    --orange-text: #f47c20;
    --green-text: #8dc21f;
    --yellow: #fdd05a;
    --yellow-deep: #f6ac2f;
    --ring: #ececec;
    --footer-bg: #2e2d25;
    --white: #ffffff;
  }
  * { box-sizing: border-box; margin: 0; padding: 0; }
  html, body { width: 1200px; height: 1018px; overflow: hidden; background: var(--white); }
  body { position: relative; font-family: "PT Sans", sans-serif; color: var(--ink); }

  .site-header { position: absolute; left: 0; top: 0; width: 1200px; height: 92px; background: var(--header-bg); }
  .brand { position: absolute; left: 115px; top: 16px; font-family: "Oswald", sans-serif; font-weight: 500; font-size: 40px; line-height: 50px; color: var(--ink); letter-spacing: -0.5px; }
  .search { position: absolute; left: 835px; top: 16px; display: flex; gap: 6px; }
  .search-field { width: 227px; height: 33px; background: var(--white); border: 1px solid #cfcfcf; }
  .search-button { width: 33px; height: 33px; background: #4a4a4a; display: flex; align-items: center; justify-content: center; }
  .top-nav { position: absolute; right: 107px; top: 66px; font-size: 14px; color: #222; }
  .top-nav span { margin: 0 6px; }

  .hero { position: absolute; left: 0; top: 92px; width: 1200px; height: 423px; }
  .hero-photo { position: absolute; inset: 0; background: radial-gradient(ellipse at 60% 40%, var(--hero-light) 0%, #bdbdbd 45%, var(--hero-dark) 100%); }
  .hero-copy { position: absolute; left: 520px; width: 442px; top: 60px; text-align: center; font-family: "Sansita", sans-serif; font-weight: 800; color: var(--ink); }
  .hero-copy .line-s { font-size: 31px; line-height: 40px; display: block; }
  .hero-copy .line-l { font-size: 42px; line-height 52px; display: block; margin: 10px 0 12px; }
  .hero-actions { position: absolute; top: 324px; left: 449px; display: flex; gap: 23px; }
  .btn { width: 248px; height: 50px; border-radius: 6px; font-family: "Sansita", sans-serif; font-weight: 800; font-size: 22px; color: var(--ink); display: flex; align-items: center; justify-content: center; letter-spacing: 0.3px; }
  .btn-signup { background: linear-gradient(var(--green), var(--green-dark)); border: 1px solid #5d9420; }
  .btn-plans { background: linear-gradient(var(--yellow), var(--yellow-deep)); border: 1px solid #c98b1e; }
  .hero-arrow { position: absolute; top: 210px; }
  .hero-arrow.prev { left: 96px; }
  .hero-arrow.next { right: 96px; }

  .guide-card { position: absolute; top: 619px; width: 490px; height: 299px; background: var(--white); box-shadow: inset 0 0 22px rgba(0,0,0,0.16); padding: 0 21px; }
  .guide-card.left { left: 95px; }
  .guide-card.right { left: 608px; }
  .guide-card::after { content: ""; position: absolute; left: 40px; right: 40px; bottom: -22px; height: 8px; border-radius: 50%; background: rgba(0,0,0,0.12); filter: blur(4px); }
  .badge { position: absolute; top: 532px; width: 150px; height: 150px; border-radius: 50%; background: var(--ring); display: flex; align-items: center; justify-content: center; z-index: 2; }
  .badge.left { left: 257px; }
  .badge.right { left: 779px; }
  .badge-core { width: 116px; height: 116px; border-radius: 50%; display: flex; align-items: center; justify-content: center; }
  .badge.left .badge-core { background: linear-gradient(var(--orange), var(--orange-deep)); }
  .badge.right .badge-core { background: linear-gradient(#94cc00, #7fb800); }
  .guide-title { margin-top: 70px; height: 90px; display: flex; align-items: center; justify-content: center; text-align: center; font-weight: 700; font-size: 18px; line-height: 37px; }
  .left .guide-title { color: var(--orange-text); }
  .right .guide-title { color: var(--green-text); }
  .guide-text { margin-top: 14px; font-size: 13.5px; line-height: 25px; text-align: justify; color: #111; }

  .site-footer { position: absolute; left: 0; top: 964px; width: 1200px; height: 54px; background: var(--footer-bg); color: #e8e8e8; }
  .legal { position: absolute; left: 98px; top: 19px; font-size: 11.5px; }
  .social { position: absolute; left: 943px; top: 971px; display: flex; gap: 2px; }
  .social span { width: 38px; height: 38px; border-radius: 50%; background: var(--white); border: 1px solid #ccc; display: block; }
</style>
</head>
<body>
  <header class="site-header">
    <div class="brand">Pingo</div>
    <div class="search">
      <div class="search-field"></div>
      <div class="search-button">
        <svg width="12" height="12" viewBox="0 0 12 12"><circle cx="5" cy="5" r="3.5" fill="none" stroke="#fff" stroke-width="1.8"/><line x1="7.5" y1="7.5" x2="11" y2="11" stroke="#fff" stroke-width="2"/></svg>
      </div>
    </div>
    <nav class="top-nav">How it works<span>|</span>Support<span>|</span>Login</nav>
  </header>

  <section class="hero">
    <div class="hero-photo" role="img" aria-label="Grey photo of a fingertip touching floating envelope icons over a dotted world map and hexagons"></div>
    <svg class="hero-arrow prev" width="24" height="46" viewBox="0 0 24 46"><polyline points="22,2 2,23 22,44" fill="none" stroke="#fff" stroke-width="1.5"/></svg>
    <svg class="hero-arrow next" width="24" height="46" viewBox="0 0 24 46"><polyline points="2,2 22,23 2,44" fill="none" stroke="#fff" stroke-width="1.5"/></svg>
    <h1 class="hero-copy">
      <span class="line-s">We provide an</span>
      <span class="line-l">easy way for people to</span>
      <span class="line-s">manage email for a</span>
      <span class="line-l">custom domain name</span>
    </h1>
    <div class="hero-actions">
      <div class="btn btn-signup">Get Started Here</div>
      <div class="btn btn-plans">Compare Plans</div>
    </div>
  </section>

  <div class="badge left"><div class="badge-core">
    <svg width="34" height="32" viewBox="0 0 34 32" fill="#fff"><ellipse cx="12" cy="5" rx="10" ry="4"/><path d="M2 8c0 2 4.5 4 10 4s10-2 10-4v5c0 2-4.5 4-10 4S2 15 2 13z"/><path d="M2 16c0 2 4.5 4 10 4 1 0 2 0 3-.2V24c-1 .1-2 .2-3 .2-5.5 0-10-2-10-4z"/><circle cx="25" cy="23" r="5" fill="none" stroke="#fff" stroke-width="3.5" stroke-dasharray="3 2"/><circle cx="25" cy="23" r="2"/></svg>
  </div></div>
  <div class="badge right"><div class="badge-core">
    <svg width="30" height="34" viewBox="0 0 30 34" fill="#fff"><circle cx="12" cy="8" r="7"/><path d="M0 30c0-8 5-13 12-13 3 0 5 .8 7 2.2A9 9 0 0 0 15 30z"/><circle cx="22" cy="26" r="7" fill="#fff"/><path d="M22 22v8M18 26h8" stroke="#86bd00" stroke-width="2"/></svg>
  </div></div>

  <article class="guide-card left">
    <h2 class="guide-title">How to configure your Skyveil DNS to use<br>Pingo. qz</h2>
    <p class="guide-text">Lorem ipsum dolor sit amet, consectetur adipisicing elit, sed do eiusmod tempor incididunt ut labore et dolore magna aliqua. Ut enim ad minim veniam, quis nostrud exercitation ullamco laboris nisi ut aliquip ex ea commodo consequat.</p>
  </article>
  <article class="guide-card right">
    <h2 class="guide-title">Use pingo.qz with your HostMarigold domain<br>registration for Reliable email forwarding</h2>
    <p class="guide-text">Lorem ipsum dolor sit amet, consectetur adipisicing elit, sed do eiusmod tempor incididunt ut labore et dolore magna aliqua. Ut enim ad minim veniam, quis nostrud exercitation ullamco laboris nisi ut aliquip ex ea commodo consequat.</p>
  </article>

  <footer class="site-footer">
    <p class="legal">© 2014 Company Name.&nbsp; All right reserved.&nbsp; Term of Use</p>
  </footer>
  <div class="social" aria-label="Social links"><span></span><span></span><span></span><span></span></div>
</body>
</html>
```